Real Estate Website - Phase I

We are looking to re-design our company website completely.
This will be for a real estate company which focuses on multiple lines of business/customers, including

1) Buyers - Investors, Owner Occupants
2) Sellers - Short Sales, Limited Services/Flat Fee, and Corporate/REO clients (the last being our core current customer)
3) Other Services: Default Services, Institutional Property Management, Field and Inspection Services
4) Agent FAQ's, instructions, etc to tie into our web-based offer management systems

For a brief understanding of what we do - Please see www.tvbalp.com. Current site does not address all of our current services.

Website must be able to be edited/added onto over time. We are also looking at redirects so that certain pages/sections can be given unique domain names to drive core customers to.

We work both with normal agents and buyers and large scale financial institutions, therefore our focus must be specific to each unique group based on the applicable page(s).

We had an incorrect amount in this brief.  It has since been corrected.

Please re-review.

Industry/Entity Type

Real Estate

Requirements
Must have
• *Property Search/Display - By various criteria AND by map
*Property Management back end for putting in new properties
*MObile Version or Mobile Friendly
*Analytics
*Contact Management and Lead Capture functions, including ability to export or use from site for email marketing campaigns. Lead capture must be able to sort by various criteria to tailor campaigns, ability to send out auto notices to staff and those signing up, etc.
* Signup option w/ functions for viewing not yet on market properties (subscription). This needs to be able to let buyers set search criteria and be auto notified whenever a property was listed or adjusted that met their criteria.
* SEO Optimization
* Syndication options to allow ease of syndication
* FAQ's and assistance pages to agents working with us
* Blog, social media boxes
* Ability for buyers to submit initial offers direct
* Functions and pages specific to below, with ability to cross promote and track (inquiry forms, etc to the below)
*Dedicated or preferred lender(s)
* Preferred vendors, etc

```html
<!DOCTYPE html>
<html lang="en">
<head>
<meta charset="utf-8">
<title>Harbor Line REO</title>
<link href="https://fonts.googleapis.com/css2?family=PT+Sans:wght@400;700&display=swap" rel="stylesheet">
<style>
:root{
  --cream:#f6ead8;
  --orange:#eca42a;
  --orange-dark:#d98f17;
  --navy:#2b2f7a;
  --navy-text:#2a3270;
  --text:#4a4a4a;
  --muted:#6b6b6b;
  --panel:#fbf3e7;
  --line:#e3d6c2;
  --footer:#3b3a38;
}
*{box-sizing:border-box;margin:0;padding:0}
html,body{width:878px;height:1200px;overflow:hidden}
body{background:var(--cream);font-family:"PT Sans",sans-serif;color:var(--text);position:relative}
.abs{position:absolute}
.top-rule{left:0;top:0;width:878px;height:4px;background:var(--orange)}
.user-bar{left:562px;top:0;width:204px;height:25px;background:var(--orange);border-radius:0 0 14px 14px;color:#fff;font-size:9px;display:flex;align-items:center;justify-content:center;gap:6px}
.brand{left:109px;top:22px;display:flex;align-items:center;gap:6px}
.brand-mark{width:52px;height:58px;background:var(--navy)}
.brand-name{font-size:24px;font-weight:700;color:var(--navy-text);line-height:1.05;width:160px}
.search{left:602px;top:46px;width:164px;height:22px;display:flex}
.search-field{flex:1;background:#fff;border:1px solid #e0d5c4}
.search-btn{width:23px;background:var(--orange);display:flex;align-items:center;justify-content:center}
.hero{left:0;top:97px;width:878px;height:384px;background:linear-gradient(180deg,#6fa3cf 0%,#cfd9df 30%,#e6d6b8 45%,#8c6e52 65%,#c9b89a 82%,#6b9a3c 100%)}
.nav{left:0;top:93px;width:878px;height:36px}
.nav-band{left:105px;top:0;width:668px;height:36px;background:var(--orange);border-radius:0 0 18px 18px}
.nav-items{left:120px;top:0;height:36px;display:flex;align-items:stretch;list-style:none}
.nav-items li{color:#fff;font-size:9.5px;text-transform:uppercase;display:flex;align-items:center;padding:0 16px}
.nav-items li.active{background:#f2b545}
.dots{left:110px;top:457px;display:flex;gap:4px}
.dots span{width:9px;height:9px;border-radius:50%;background:#2e2e1e;opacity:.8}
.feature{top:500px;width:206px;height:118px;background:#fff;border:1px solid #e4d8c4;padding:4px}
.feature-img{width:100%;height:100%;position:relative;overflow:hidden}
.feature-label{position:absolute;left:0;bottom:10px;width:160px;height:34px;background:rgba(236,164,42,.9);clip-path:polygon(0 0,88% 0,100% 100%,0 100%);display:flex;align-items:center;gap:8px;padding-left:8px;color:#fff;font-size:14px;text-transform:uppercase}
.chev{width:17px;height:17px;border-radius:50%;background:#fff;display:flex;align-items:center;justify-content:center}
.filters{left:109px;top:637px;width:473px;height:35px;background:var(--panel);border:1px solid #ddd0bb;display:flex;gap:23px;padding:7px 8px}
.select{width:135px;height:19px;background:linear-gradient(#fdfdfd,#e6e2dc);border:1px solid #bcb6ad;border-radius:4px;font-size:8px;display:flex;align-items:center;padding-left:7px;position:relative}
.select i{position:absolute;right:0;top:0;width:15px;height:17px;background:var(--navy);border-radius:0 3px 3px 0;display:flex;align-items:center;justify-content:center}
.section-title{left:109px;top:686px;font-size:14px;font-weight:700;color:#555}
.view-all{left:500px;top:684px;width:76px;height:21px;background:var(--navy);color:#fff;font-size:9px;display:flex;align-items:center;justify-content:center;gap:6px;border-radius:0 12px 12px 0}
.divider{left:109px;top:712px;width:467px;height:1px;background:var(--line)}
.listing{left:109px;width:467px;height:124px;background:var(--panel)}
.listing-thumb{position:absolute;left:7px;top:7px;width:127px;height:109px;background:#fff;border:1px solid #e7dccb;padding:4px}
.listing-thumb div{width:100%;height:100%}
.listing-title{position:absolute;left:149px;top:11px;width:318px;height:28px;background:var(--orange);clip-path:polygon(4% 0,100% 0,100% 100%,0 100%);color:#fff;font-size:11px;display:flex;align-items:center;padding-left:20px}
.price{position:absolute;right:0;top:5px;height:19px;width:96px;background:var(--navy);border-radius:10px 0 0 10px;color:#fff;font-size:8.5px;display:flex;align-items:center;justify-content:center}
.specs{position:absolute;left:169px;top:52px;display:grid;grid-template-columns:150px 150px;row-gap:12px;font-size:8.8px;color:#444}
.sidebox{left:589px;width:180px;background:var(--panel);border:1px solid #ddd0bb;padding:8px}
.sidebox h3{font-size:12px;font-weight:700;color:var(--navy-text);text-transform:uppercase;padding:0 1px 7px;border-bottom:1px solid var(--line);margin-bottom:8px}
.post{font-size:7.5px;line-height:1.3;text-align:justify;padding-bottom:6px;margin-bottom:6px;border-bottom:1px solid var(--line)}
.post:last-child{border:0}
.post b{display:block;color:var(--orange-dark);font-size:9px;font-weight:700}
.sidebox p{font-size:7.5px;line-height:1.3;text-align:justify;margin-bottom:9px}
.email{height:20px;background:#fff;border:1px solid #cfc6b8;border-radius:4px;font-size:7.5px;display:flex;align-items:center;padding-left:6px;margin:2px 2px 9px}
.submit{width:63px;height:20px;background:linear-gradient(#f6be4c,var(--orange-dark));border-radius:4px;color:#fff;font-size:10px;display:flex;align-items:center;justify-content:center;margin-left:2px}
.footer{left:0;top:1141px;width:878px;height:59px;background:var(--footer);color:#ddd;font-size:7.5px}
.footer-links{left:109px;top:13px}
.copy{left:109px;top:34px}
.social{left:637px;top:16px;display:flex;gap:6px}
.social span{width:22px;height:22px}
</style>
</head>
<body>
<div class="abs top-rule"></div>
<div class="abs user-bar"><span>Welcome, Guest</span><span>Log In</span><span>|</span><span>Sign Up</span><span>|</span><span>FAQs</span></div>

<div class="abs brand">
  <div class="brand-mark"></div>
  <div class="brand-name">HARBOR LINE REO</div>
</div>

<div class="abs search">
  <div class="search-field"></div>
  <div class="search-btn"><svg width="11" height="11" viewBox="0 0 11 11"><circle cx="4.5" cy="4.5" r="3" fill="none" stroke="#fff" stroke-width="1.6"/><line x1="6.8" y1="6.8" x2="10" y2="10" stroke="#fff" stroke-width="2"/></svg></div>
</div>

<div class="abs hero" role="img" aria-label="Photo of a stucco and stone home with an arched entry, palms and a lawn"></div>

<div class="abs nav">
  <div class="abs nav-band"></div>
  <ul class="abs nav-items">
    <li class="active">Home</li><li>Our Listings</li><li>Our Listings</li><li>Buyers</li><li>Short Sales</li><li>Agents</li><li>Asset Managers</li><li>Contact</li>
  </ul>
</div>

<div class="abs dots"><span></span><span></span><span></span></div>

<div class="abs feature" style="left:109px">
  <div class="feature-img" role="img" aria-label="Couple pointing at a cloud shaped like a house in a blue sky" style="background:linear-gradient(180deg,#4f8fd0,#9cc4e8 60%,#7fa25a)">
    <div class="feature-label"><span class="chev"><svg width="7" height="8" viewBox="0 0 7 8"><path d="M1 1l4 3-4 3" fill="none" stroke="#eca42a" stroke-width="1.8"/></svg></span>Buyers</div>
  </div>
</div>
<div class="abs feature" style="left:336px">
  <div class="feature-img" role="img" aria-label="Agent holding a for sale sign in front of a house" style="background:linear-gradient(180deg,#6c9ccc,#8a7a66 55%,#4f6b35)">
    <div class="feature-label"><span class="chev"><svg width="7" height="8" viewBox="0 0 7 8"><path d="M1 1l4 3-4 3" fill="none" stroke="#eca42a" stroke-width="1.8"/></svg></span>Agents</div>
  </div>
</div>
<div class="abs feature" style="left:563px">
  <div class="feature-img" role="img" aria-label="Asset manager meeting with a couple" style="background:linear-gradient(180deg,#f1ece6,#d9cfc4 60%,#c7b7a8)">
    <div class="feature-label" style="width:190px"><span class="chev"><svg width="7" height="8" viewBox="0 0 7 8"><path d="M1 1l4 3-4 3" fill="none" stroke="#eca42a" stroke-width="1.8"/></svg></span>Asset Manager</div>
  </div>
</div>

<div class="abs filters">
  <div class="select">Location<i><svg width="7" height="5" viewBox="0 0 7 5"><path d="M0 0h7L3.5 5z" fill="#fff"/></svg></i></div>
  <div class="select">Properties by Type<i><svg width="7" height="5" viewBox="0 0 7 5"><path d="M0 0h7L3.5 5z" fill="#fff"/></svg></i></div>
  <div class="select">Properties by Price<i><svg width="7" height="5" viewBox="0 0 7 5"><path d="M0 0h7L3.5 5z" fill="#fff"/></svg></i></div>
</div>

<div class="abs section-title">Latest Properties</div>
<div class="abs view-all">VIEW ALL <svg width="6" height="8" viewBox="0 0 6 8"><path d="M1 1l3.5 3L1 7" fill="none" stroke="#fff" stroke-width="1.6"/></svg></div>
<div class="abs divider"></div>

<div class="abs listing" style="top:725px">
  <div class="listing-thumb"><div role="img" aria-label="Balcony of an apartment block with a sale sign" style="background:linear-gradient(180deg,#8a8f95,#b8b0a4 55%,#5a4a40)"></div></div>
  <div class="listing-title">Linden Estate Fully Furnished (3 bdr)<span class="price">For Sale : €330,000</span></div>
  <div class="specs"><span>Area : 117 (Sq.M.)</span><span>Property ID : 14353</span><span>Bedrooms : 3</span><span>Posted on : March 2, 2013</span><span>Bathrooms :</span><span>Seller : Marlow Realty Group</span></div>
</div>
<div class="abs listing" style="top:862px">
  <div class="listing-thumb"><div role="img" aria-label="Pool area with palm trees and a white tent" style="background:linear-gradient(180deg,#3d8fd8,#8cc2e6 45%,#6f9a4a 70%,#4aa0d0)"></div></div>
  <div class="listing-title">Linden Estate Fully Furnished (3 bdr)<span class="price">For Sale : €330,000</span></div>
  <div class="specs"><span>Area : 117 (Sq.M.)</span><span>Property ID : 14353</span><span>Bedrooms : 3</span><span>Posted on : March 2, 2013</span><span>Bathrooms :</span><span>Seller : Marlow Realty Group</span></div>
</div>
<div class="abs listing" style="top:1000px">
  <div class="listing-thumb"><div role="img" aria-label="Large window reflecting garden greenery" style="background:linear-gradient(180deg,#6a8a5a,#2e3a2a 40%,#5d7a4a)"></div></div>
  <div class="listing-title">Linden Estate Fully Furnished (3 bdr)<span class="price">For Sale : €330,000</span></div>
  <div class="specs"><span>Area : 117 (Sq.M.)</span><span>Property ID : 14353</span><span>Bedrooms : 3</span><span>Posted on : March 2, 2013</span><span>Bathrooms :</span><span>Seller : Marlow Realty Group</span></div>
</div>

<aside class="abs sidebox" style="top:637px;height:199px">
  <h3>Recent Blog</h3>
  <div class="post"><b>Sed ut perspiciatis unde omnis iste nat</b>sit voluptatem accusantium doloremque laudantium, totam rem aperiam, eaque ipsa quae ab illo inventore</div>
  <div class="post"><b>Sed ut perspiciatis unde omnis iste nat</b>sit voluptatem accusantium doloremque laudantium, totam rem aperiam, eaque ipsa quae ab illo inventore</div>
  <div class="post"><b>Sed ut perspiciatis unde omnis iste nat</b>sit voluptatem accusantium doloremque laudantium, totam rem aperiam, eaque ipsa quae ab illo inventore</div>
</aside>

<aside class="abs sidebox" style="top:843px;height:177px">
  <h3>Selling Property</h3>
  <p>Sed ut perspiciatis unde omnis iste natus error sit voluptatem accusantium doloremque laudantium, totam rem aperiam, eaque ipsa quae ab illo inventore veritatis et quasi architecto beatae vitae dicta sunt explicabo.</p>
  <p>Nemo enim ipsam voluptatem quia voluptas sit aspernatur aut odit aut fugit, sed quia Sed ut perspiciatis unde omnis</p>
  <p>iste natus error sit voluptatem accusantium doloremque laudantium, totam rem aperiam, eaque ipsa quae ab illo inventore veritatis et</p>
</aside>

<aside class="abs sidebox" style="top:1027px;height:98px">
  <h3>Subscribe to Newsletter!</h3>
  <div class="email">Enter Email Address</div>
  <div class="submit">SUBMIT</div>
</aside>

<footer class="abs footer">
  <div class="abs footer-links">Privacy Policy | Agent Login | Site Map</div>
  <div class="abs copy">Copyright © 2013 Harbor Line REO. All rights reserved.</div>
  <div class="abs social">
    <span style="background:#3b5bb0"></span><span style="background:#2fa8df"></span><span style="background:#d9473a"></span><span style="background:#c8231d"></span><span style="background:#f08a1c"></span>
  </div>
</footer>
</body>
</html>
```